The Linen Loft Co

We need a business card design for our wardrobe company.
Please visit our website www.gentlelinenlofts.com to get an idea of who we are.

```html
<!DOCTYPE html>
<html lang="en">
<head>
<meta charset="utf-8">
<title>The Linen Loft Co — Business Card</title>
<link rel="stylesheet" href="https://fonts.googleapis.com/css2?family=Arimo:wght@700&family=Lato:wght@400&family=Montserrat:wght@500&family=Fira+Sans:wght@400&display=swap">
<style>
  :root {
    --page-bg: #5e5e5e;
    --card-bg: #1a1a1a;
    --gold: #9a8458;
    --text-light: #f2f2f2;
  }
  * { margin: 0; padding: 0; box-sizing: border-box; }
  html, body {
    width: 1200px;
    height: 1200px;
    overflow: hidden;
    background: var(--page-bg);
  }
  .card {
    position: absolute;
    left: 60px;
    top: 286px;
    width: 1080px;
    height: 628px;
    background: var(--card-bg);
    border-radius: 45px;
  }
  .brand-mark {
    position: absolute;
    left: 240px;
    top: 84px;
    width: 129px;
    height: 129px;
    background: var(--gold);
  }
  .brand-name {
    position: absolute;
    left: 447px;
    top: 96px;
    font-family: "Montserrat", sans-serif;
    font-weight: 500;
    font-size: 39px;
    letter-spacing: 1.5px;
    color: var(--gold);
    white-space: nowrap;
  }
  .brand-tagline {
    position: absolute;
    left: 489px;
    top: 156px;
    font-family: "Montserrat", sans-serif;
    font-weight: 500;
    font-size: 33px;
    color: var(--gold);
    white-space: nowrap;
  }
  .person-name {
    position: absolute;
    left: 55px;
    top: 307px;
    font-family: "Arimo", sans-serif;
    font-weight: 700;
    font-size: 41px;
    color: var(--gold);
  }
  .person-role {
    position: absolute;
    left: 55px;
    top: 364px;
    font-family: "Fira Sans", sans-serif;
    font-size: 34px;
    color: var(--text-light);
  }
  .contact-list {
    position: absolute;
    left: 52px;
    top: 432px;
    list-style: none;
  }
  .contact-item {
    display: flex;
    align-items: center;
    height: 37px;
    font-family: "Lato", sans-serif;
    font-size: 24px;
    color: var(--text-light);
  }
  .contact-icon {
    width: 18px;
    height: 18px;
    margin-right: 14px;
    fill: var(--gold);
  }
  .address {
    position: absolute;
    right: 56px;
    top: 506px;
    text-align: right;
    font-family: "Lato", sans-serif;
    font-style: normal;
    font-size: 26px;
    line-height: 34px;
    color: var(--text-light);
    letter-spacing: 0.5px;
  }
</style>
</head>
<body>
  <main class="card">
    <div class="brand-mark"></div>
    <div class="brand-name">THE LINEN LOFT CO</div>
    <div class="brand-tagline">Crafted for Every Corner</div>

    <div class="person-name">Dana Holloway</div>
    <div class="person-role">Manager</div>

    <ul class="contact-list">
      <li class="contact-item">
        <svg class="contact-icon" viewBox="0 0 24 24" aria-hidden="true"><path d="M6.6 10.8a15.1 15.1 0 0 0 6.6 6.6l2.2-2.2a1 1 0 0 1 1-.25 11.4 11.4 0 0 0 3.6.6 1 1 0 0 1 1 1V20a1 1 0 0 1-1 1A17 17 0 0 1 3 4a1 1 0 0 1 1-1h3.5a1 1 0 0 1 1 1c0 1.25.2 2.45.6 3.6a1 1 0 0 1-.25 1z"/></svg>
        555-214-3370
      </li>
      <li class="contact-item">
        <svg class="contact-icon" viewBox="0 0 24 24" aria-hidden="true"><path d="M7 1h10a2 2 0 0 1 2 2v18a2 2 0 0 1-2 2H7a2 2 0 0 1-2-2V3a2 2 0 0 1 2-2zm0 3v15h10V4z"/></svg>
        555-382-1946
      </li>
      <li class="contact-item">
        <svg class="contact-icon" viewBox="0 0 24 24" aria-hidden="true"><path d="M2 5h20v14H2zm2 2v.5l8 5 8-5V7z"/></svg>
        info@gentlelinenlofts.com
      </li>
      <li class="contact-item">
        <svg class="contact-icon" viewBox="0 0 24 24" aria-hidden="true"><circle cx="12" cy="12" r="10"/></svg>
        www.gentlelinenlofts.com
      </li>
    </ul>

    <address class="address">
      18-20 Marlow Orchard<br>Street 480112, USA
    </address>
  </main>
</body>
</html>
```